BRIX GUARDING WEBSITE BANNER DESIGN OF AWESOME

Please take a look at the attached Banner. I want a redesign Idea. The requirements are below.

1)Must Use Website Background
2)Must Use Photo Provided
3)Must Include Button
4)Website the banner will be used on you can see the current at the bottom of the page: https://b.lunorvex.com

Target Market(s)

Anyone Seeking Security Guard Services

```html
<!DOCTYPE html>
<html lang="en">
<head>
<meta charset="utf-8">
<title>BRIX GUARDING – Website Banner</title>
<link href="https://fonts.googleapis.com/css2?family=Poppins:wght@400;500;600;700&family=Montserrat:wght@400;500&display=swap" rel="stylesheet">
<style>
  :root {
    --page-bg: #f8f8f8;
    --navy: #1d4e7d;
    --navy-light: #225a8c;
    --navy-dark: #17385f;
    --navy-band: #1b4876;
    --footer: #173d66;
    --accent: #f7b21b;
    --cta-blue: #1565c8;
    --white: #ffffff;
    --photo-a: #0f1e33;
    --photo-b: #3c6a98;
  }
  * { box-sizing: border-box; margin: 0; padding: 0; }
  html, body { width: 1200px; height: 1195px; overflow: hidden; background: var(--page-bg); }
  body { font-family: "Poppins", sans-serif; color: var(--white); position: relative; }

  .site { position: absolute; left: 0; top: 0; width: 1200px; background: var(--navy); }

  .site-nav { height: 60px; background: var(--navy); position: relative; font-size: 13px; font-weight: 500; }
  .site-nav a { position: absolute; top: 21px; color: var(--white); text-decoration: none; letter-spacing: .2px; }
  .site-nav a.is-active { color: var(--accent); }
  .site-nav .caret { display: inline-block; margin-left: 6px; border: 4px solid transparent; border-top: 5px solid var(--white); border-bottom: 0; vertical-align: middle; }
  .site-nav .divider { position: absolute; left: 936px; top: 20px; width: 1px; height: 18px; background: #6fa0d0; }
  .site-nav .quote-btn { top: 9px; left: 942px; height: 38px; padding: 0 14px; line-height: 38px; background: var(--cta-blue); border-radius: 20px; font-weight: 600; border: 2px solid #2b7fe0; }

  .hero { position: relative; width: 1200px; height: 437px; overflow: hidden; }
  .hero svg.hero-bg { position: absolute; inset: 0; }
  .hero-title { position: absolute; left: 136px; top: 84px; font-size: 61px; font-weight: 600; line-height: 1; letter-spacing: -.5px; }
  .hero-tagline { position: absolute; left: 138px; top: 159px; font-size: 31px; font-weight: 600; color: var(--accent); }
  .hero-cta { position: absolute; left: 137px; top: 229px; width: 159px; height: 38px; background: var(--accent); border-radius: 4px; color: var(--navy-dark); font-size: 19px; font-weight: 600; text-align: center; line-height: 38px; }
  .hero-features { position: absolute; top: 320px; left: 0; }
  .feature { position: absolute; width: 150px; font-size: 19px; font-weight: 600; line-height: 24px; }
  .feature svg { position: absolute; left: -34px; top: -4px; }

  .offices { position: relative; height: 175px; }
  .office { position: absolute; top: 35px; font-family: "Montserrat", sans-serif; }
  .office h3 { font-size: 20px; font-weight: 500; color: var(--accent); margin-bottom: 14px; }
  .office li { list-style: none; font-size: 13px; height: 26px; display: flex; align-items: center; gap: 11px; }
  .office li svg { flex: none; }

  .site-footer { height: 36px; background: var(--footer); font-size: 11px; text-align: center; line-height: 36px; position: relative; }
  .to-top { position: absolute; right: 20px; top: -4px; width: 30px; height: 28px; background: #123253; }

  .banner { position: absolute; left: 0; top: 740px; }
</style>
</head>
<body>

<section class="site">
  <nav class="site-nav">
    <a class="is-active" style="left:284px">HOME</a>
    <a style="left:350px">ABOUT US</a>
    <a style="left:443px">SERVICES<span class="caret"></span></a>
    <a style="left:550px">EMPLOYMENT</a>
    <a style="left:710px">CONTACT US<span class="caret"></span></a>
    <a style="left:840px">CLIENT LOGIN</a>
    <span class="divider"></span>
    <a class="quote-btn">REQUEST A QUOTE</a>
  </nav>

  <div class="hero">
    <svg class="hero-bg" width="1200" height="437" viewBox="0 0 1200 437">
      <defs>
        <linearGradient id="photoTone" x1="0" y1="1" x2="1" y2="0">
          <stop offset="0" stop-color="var(--photo-a)"/>
          <stop offset="1" stop-color="var(--photo-b)"/>
        </linearGradient>
      </defs>
      <rect width="1200" height="437" fill="var(--navy)"/>
      <polygon points="0,0 133,0 27,293 0,293" fill="var(--navy-dark)"/>
      <polygon points="133,0 826,0 720,293 27,293" fill="var(--navy-light)"/>
      <polygon points="0,293 720,293 620,437 0,437" fill="var(--navy-band)"/>
      <polygon points="0,293 560,293 160,437 0,437" fill="var(--navy)" opacity=".55"/>
      <g role="img" aria-label="Photo: security guard in dark uniform shining a flashlight up a stairway">
        <polygon points="826,0 1200,0 1200,437 607,437" fill="url(#photoTone)"/>
      </g>
      <polygon points="826,0 840,0 720,215 706,215" fill="var(--accent)"/>
      <polygon points="1200,120 1200,150 1098,437 1082,437" fill="var(--accent)"/>
    </svg>
    <h1 class="hero-title">Get secured today</h1>
    <p class="hero-tagline">We take your security personal.</p>
    <span class="hero-cta">GET Started</span>
    <div class="hero-features">
      <div class="feature" style="left:172px"><svg width="28" height="26" viewBox="0 0 28 26"><path d="M2 13 L10 22 L26 2" fill="none" stroke="var(--accent)" stroke-width="4"/></svg>No Binding<br>Contracts</div>
      <div class="feature" style="left:350px"><svg width="28" height="26" viewBox="0 0 28 26"><path d="M2 13 L10 22 L26 2" fill="none" stroke="var(--accent)" stroke-width="4"/></svg>24x7<br>Dispatch</div>
      <div class="feature" style="left:497px"><svg width="28" height="26" viewBox="0 0 28 26"><path d="M2 13 L10 22 L26 2" fill="none" stroke="var(--accent)" stroke-width="4"/></svg>Client<br>Portal</div>
    </div>
  </div>

  <div class="offices">
    <div class="office" style="left:103px">
      <h3>Miami Office:</h3>
      <ul>
        <li><svg width="14" height="14" viewBox="0 0 14 14"><path d="M7 1a4 4 0 0 1 4 4c0 3-4 8-4 8S3 8 3 5a4 4 0 0 1 4-4z" fill="none" stroke="#fff" stroke-width="1.4"/><circle cx="7" cy="5" r="1.4" fill="#fff"/></svg>Miami, FL</li>
        <li><svg width="14" height="14" viewBox="0 0 14 14"><rect x="1" y="3" width="12" height="9" fill="none" stroke="#fff" stroke-width="1.4"/><path d="M1 3l6 5 6-5" fill="none" stroke="#fff" stroke-width="1.4"/></svg>info@brixguarding.com</li>
        <li><svg width="14" height="14" viewBox="0 0 14 14"><rect x="3" y="1" width="8" height="12" rx="1.5" fill="none" stroke="#fff" stroke-width="1.6"/></svg>+1 (555) 310-4821</li>
      </ul>
    </div>
    <div class="office" style="left:441px">
      <h3>FTL Office:</h3>
      <ul>
        <li><svg width="14" height="14" viewBox="0 0 14 14"><circle cx="7" cy="7" r="5.5" fill="none" stroke="#fff" stroke-width="1.4"/><circle cx="7" cy="7" r="2" fill="#fff"/></svg>Fort Lauderdale, FL</li>
        <li><svg width="14" height="14" viewBox="0 0 14 14"><rect x="1" y="3" width="12" height="9" fill="none" stroke="#fff" stroke-width="1.4"/><path d="M1 3l6 5 6-5" fill="none" stroke="#fff" stroke-width="1.4"/></svg>info@brixguarding.com</li>
        <li><svg width="14" height="14" viewBox="0 0 14 14"><rect x="3" y="1" width="8" height="12" rx="1.5" fill="none" stroke="#fff" stroke-width="1.6"/></svg>+1 (555) 472-9016</li>
      </ul>
    </div>
    <div class="office" style="left:779px">
      <h3>Boca Office:</h3>
      <ul>
        <li><svg width="14" height="14" viewBox="0 0 14 14"><circle cx="7" cy="7" r="5.5" fill="none" stroke="#fff" stroke-width="1.4"/><circle cx="7" cy="7" r="2" fill="#fff"/></svg>Boca Raton, FL</li>
        <li><svg width="14" height="14" viewBox="0 0 14 14"><rect x="1" y="3" width="12" height="9" fill="none" stroke="#fff" stroke-width="1.4"/><path d="M1 3l6 5 6-5" fill="none" stroke="#fff" stroke-width="1.4"/></svg>info@brixguarding.com</li>
        <li><svg width="14" height="14" viewBox="0 0 14 14"><rect x="3" y="1" width="8" height="12" rx="1.5" fill="none" stroke="#fff" stroke-width="1.6"/></svg>+1 (555) 608-2397</li>
      </ul>
    </div>
  </div>

  <footer class="site-footer">
    Copyright © 2020 BRIX GUARDING | All rights reserved | Site Map | FL. Lic # B 0000000 | Website designed by NorthPixel.com
    <span class="to-top"><svg width="30" height="28" viewBox="0 0 30 28"><path d="M10 17l5-5 5 5" fill="none" stroke="#fff" stroke-width="2"/></svg></span>
  </footer>
</section>

<section class="banner hero">
  <svg class="hero-bg" width="1200" height="437" viewBox="0 0 1200 437">
    <defs>
      <linearGradient id="photoToneBanner" x1="0" y1="1" x2="1" y2="0">
        <stop offset="0" stop-color="var(--photo-a)"/>
        <stop offset="1" stop-color="var(--photo-b)"/>
      </linearGradient>
    </defs>
    <rect width="1200" height="437" fill="var(--navy)"/>
    <polygon points="0,0 133,0 27,293 0,293" fill="var(--navy-dark)"/>
    <polygon points="133,0 826,0 720,293 27,293" fill="var(--navy-light)"/>
    <polygon points="0,293 720,293 620,437 0,437" fill="var(--navy-band)"/>
    <polygon points="0,293 560,293 160,437 0,437" fill="var(--navy)" opacity=".55"/>
    <g role="img" aria-label="Photo: security guard in dark uniform shining a flashlight up a stairway">
      <polygon points="826,0 1200,0 1200,437 607,437" fill="url(#photoToneBanner)"/>
    </g>
    <polygon points="826,0 840,0 720,215 706,215" fill="var(--accent)"/>
    <polygon points="1200,120 1200,150 1098,437 1082,437" fill="var(--accent)"/>
  </svg>
  <h2 class="hero-title">Get secured today</h2>
  <p class="hero-tagline">We take your security personal.</p>
  <span class="hero-cta">GET Started</span>
  <div class="hero-features">
    <div class="feature" style="left:172px"><svg width="28" height="26" viewBox="0 0 28 26"><path d="M2 13 L10 22 L26 2" fill="none" stroke="var(--accent)" stroke-width="4"/></svg>No Binding<br>Contracts</div>
    <div class="feature" style="left:350px"><svg width="28" height="26" viewBox="0 0 28 26"><path d="M2 13 L10 22 L26 2" fill="none" stroke="var(--accent)" stroke-width="4"/></svg>24x7<br>Dispatch</div>
    <div class="feature" style="left:497px"><svg width="28" height="26" viewBox="0 0 28 26"><path d="M2 13 L10 22 L26 2" fill="none" stroke="var(--accent)" stroke-width="4"/></svg>Client<br>Portal</div>
  </div>
</section>

</body>
</html>
```